Gobal construction supply company needs new business card design

I need a business card design for my global supply company using an existing logo. i will be looking to print these on rounded corner cards with the black background version of my logo on the back. on the front white background, my logo again and my simple details.

```html
<!DOCTYPE html>
<html lang="en">
<head>
<meta charset="utf-8">
<title>Southern Forge Supply – Business Card</title>
<link href="https://fonts.googleapis.com/css2?family=Roboto:wght@400;500;700&display=swap" rel="stylesheet">
<style>
  :root {
    --backdrop: #2b2b2b;
    --card-front: #f2f2f2;
    --card-back: #1c1c1c;
    --ink: #111111;
    --ink-soft: #4a4a4a;
    --accent: #d40000;
    --rule: #c4c4c4;
    --white: #ffffff;
  }
  * { margin: 0; padding: 0; box-sizing: border-box; }
  html, body { width: 1200px; height: 960px; overflow: hidden; }
  body {
    position: relative;
    background: var(--backdrop);
    font-family: "Roboto", Arial, sans-serif;
  }
  .card {
    position: absolute;
    width: 600px;
    height: 343px;
    border-radius: 22px;
  }
  .card--front { left: 186px; top: 113px; background: var(--card-front); }
  .card--back { left: 434px; top: 511px; background: var(--card-back); }

  .identity {
    position: absolute;
    right: 366px;
    top: 149px;
    text-align: right;
  }
  .identity__name {
    font-weight: 700;
    font-size: 21px;
    color: var(--ink);
    letter-spacing: 0.3px;
    line-height: 24px;
  }
  .identity__title {
    font-weight: 500;
    font-size: 14px;
    color: var(--accent);
    line-height: 17px;
  }
  .divider {
    position: absolute;
    left: 256px;
    top: 119px;
    width: 1px;
    height: 110px;
    background: var(--rule);
  }
  .contact-list {
    position: absolute;
    left: 278px;
    top: 124px;
    list-style: none;
  }
  .contact-list li {
    display: flex;
    align-items: center;
    height: 19px;
    font-size: 14px;
    color: var(--ink-soft);
  }
  .contact-list svg {
    width: 14px;
    height: 14px;
    margin-right: 9px;
    fill: var(--ink);
  }
  .address {
    position: absolute;
    left: 0;
    right: 0;
    top: 290px;
    display: flex;
    justify-content: center;
    align-items: center;
    font-size: 14px;
    color: var(--ink-soft);
  }
  .address svg { width: 14px; height: 16px; margin-right: 7px; fill: var(--ink); }

  .brand {
    position: absolute;
    left: 0;
    right: 0;
    top: 150px;
    display: flex;
    justify-content: center;
    align-items: center;
    gap: 12px;
  }
  .brand__mark {
    width: 20px;
    height: 20px;
    background: var(--accent);
  }
  .brand__name {
    font-weight: 500;
    font-size: 21px;
    letter-spacing: 0.5px;
    color: var(--white);
  }
  .web-address {
    position: absolute;
    left: 0;
    right: 0;
    top: 290px;
    text-align: center;
    font-size: 14px;
    letter-spacing: 3px;
    color: var(--white);
  }
</style>
</head>
<body>
  <section class="card card--front" aria-label="Card front">
    <div class="identity">
      <div class="identity__name">DANIEL REEVE</div>
      <div class="identity__title">CEO/FOUNDER</div>
    </div>
    <div class="divider"></div>
    <ul class="contact-list">
      <li><svg viewBox="0 0 24 24"><path d="M6.6 10.8a15 15 0 0 0 6.6 6.6l2.2-2.2a1 1 0 0 1 1-.25 11.4 11.4 0 0 0 3.6.57 1 1 0 0 1 1 1V20a1 1 0 0 1-1 1A17 17 0 0 1 3 4a1 1 0 0 1 1-1h3.5a1 1 0 0 1 1 1c0 1.25.2 2.45.57 3.6a1 1 0 0 1-.25 1z"/></svg>612 555 0148</li>
      <li><svg viewBox="0 0 24 24"><path d="M7 1h10a2 2 0 0 1 2 2v18a2 2 0 0 1-2 2H7a2 2 0 0 1-2-2V3a2 2 0 0 1 2-2zm0 3v14h10V4zm5 15.5a1.2 1.2 0 1 0 0 2.4 1.2 1.2 0 0 0 0-2.4z"/></svg>845 555 0273</li>
      <li><svg viewBox="0 0 24 24"><path d="M6 2h12v5H6zM3 8h18a2 2 0 0 1 2 2v7h-4v5H5v-5H1v-7a2 2 0 0 1 2-2zm4 8v4h10v-4z"/></svg>471 555 0392</li>
      <li><svg viewBox="0 0 24 24"><path d="M2 5h20v14H2zm2 2v.5l8 5 8-5V7l-8 5z"/></svg>daniel@southernforgesupply.com</li>
      <li><svg viewBox="0 0 24 24"><path d="M12 2a10 10 0 1 0 0 20 10 10 0 0 0 0-20zm-1 17.9A8 8 0 0 1 4.2 10L9 14.8v1a2 2 0 0 0 2 2zm6.9-2.5A2 2 0 0 0 16 16h-1v-3a1 1 0 0 0-1-1H8v-2h2a1 1 0 0 0 1-1V7h2a2 2 0 0 0 2-2v-.4a8 8 0 0 1 2.9 12.8z"/></svg>www.southernforgesupply.com</li>
    </ul>
    <div class="address">
      <svg viewBox="0 0 24 28"><path d="M12 0a9 9 0 0 0-9 9c0 7 9 19 9 19s9-12 9-19a9 9 0 0 0-9-9zm0 12.5A3.5 3.5 0 1 1 12 5.5a3.5 3.5 0 0 1 0 7z"/></svg>
      1420 Harbor Ridge Road, Portland, Oregon 97205
    </div>
  </section>

  <section class="card card--back" aria-label="Card back">
    <div class="brand">
      <span class="brand__mark"></span>
      <span class="brand__name">SOUTHERN FORGE SUPPLY</span>
    </div>
    <div class="web-address">www.southernforgesupply.com</div>
  </section>
</body>
</html>
```